Automotive Accessories Business Card

Design a business template that match our new logo design and our industry.

https://www.qelmotorgear.com/

Target Market(s)

Aftermarket auto parts and accessories

Industry/Entity Type

automotive

Contact Information for Business Card

company logo

Font styles to use
Serif
Sans Serif

Colors
EB3D1F
EC4F4E
F09395
F8D3D4
FCEDEE

```html
<!DOCTYPE html>
<html lang="en">
<head>
<meta charset="utf-8">
<title>Qel Motor Gear Inc – Business Card</title>
<link rel="stylesheet" href="https://fonts.googleapis.com/css2?family=Montserrat:wght@400;600;700&display=swap">
<style>
  :root {
    --surface: #ebebeb;
    --card: #3c3c3d;
    --card-edge: #d71f26;
    --accent: #dc2027;
    --text: #f2f2f2;
    --muted: #cfcfcf;
    --rule: #bdbdbd;
    --deco: #5a5a5b;
  }
  * { box-sizing: border-box; margin: 0; padding: 0; }
  html, body { width: 1200px; height: 802px; overflow: hidden; }
  body {
    background: var(--surface);
    font-family: "Montserrat", Arial, sans-serif;
    position: relative;
  }
  .card {
    position: absolute;
    top: 246px;
    width: 540px;
    height: 309px;
    background: var(--card);
    border-bottom: 4px solid var(--card-edge);
    border-left: 3px solid var(--card-edge);
    box-shadow: 0 8px 22px rgba(0,0,0,.18);
    overflow: hidden;
  }
  .card--front { left: 40px; }
  .card--back { left: 620px; }

  /* front */
  .brand {
    position: absolute;
    top: 52px;
    right: 60px;
    display: flex;
    align-items: center;
    gap: 10px;
    font-weight: 700;
    font-size: 22px;
    letter-spacing: .06em;
    color: var(--text);
  }
  .brand__mark { width: 16px; height: 16px; background: var(--accent); }
  .divider {
    position: absolute;
    left: 40px;
    right: 40px;
    top: 150px;
    height: 1px;
    background: var(--rule);
  }
  .person { position: absolute; left: 40px; top: 176px; }
  .person__name {
    color: var(--accent);
    font-weight: 700;
    font-size: 17px;
    letter-spacing: .12em;
    text-transform: uppercase;
  }
  .person__role { color: var(--muted); font-size: 12px; margin: 3px 0 12px; }
  .contact { list-style: none; }
  .contact li {
    display: flex;
    align-items: center;
    gap: 8px;
    color: var(--muted);
    font-size: 12px;
    line-height: 20px;
  }
  .contact svg { width: 11px; height: 11px; fill: var(--accent); flex: none; }
  .address {
    position: absolute;
    right: 40px;
    top: 176px;
    text-align: right;
    color: var(--muted);
    font-size: 12px;
    line-height: 19px;
  }

  /* back */
  .backdrop-name {
    position: absolute;
    left: 30px;
    top: 36px;
    font-weight: 700;
    font-size: 150px;
    line-height: 1;
    letter-spacing: .02em;
    color: var(--deco);
  }
  .back-brand {
    position: absolute;
    left: 70px;
    bottom: 62px;
    display: flex;
    align-items: center;
    gap: 12px;
    font-weight: 700;
    font-size: 24px;
    letter-spacing: .06em;
    color: var(--text);
  }
  .back-brand__mark { width: 18px; height: 18px; background: var(--accent); }
</style>
</head>
<body>

<section class="card card--front">
  <div class="brand"><span class="brand__mark"></span>QEL MOTOR GEAR INC</div>
  <div class="divider"></div>
  <div class="person">
    <p class="person__name">Daniel Marsh</p>
    <p class="person__role">Manager</p>
    <ul class="contact">
      <li><svg viewBox="0 0 24 24"><path d="M6.6 10.8a15 15 0 0 0 6.6 6.6l2.2-2.2a1 1 0 0 1 1-.25 11.4 11.4 0 0 0 3.6.57 1 1 0 0 1 1 1V20a1 1 0 0 1-1 1A17 17 0 0 1 3 4a1 1 0 0 1 1-1h3.5a1 1 0 0 1 1 1c0 1.25.2 2.45.57 3.57a1 1 0 0 1-.25 1z"/></svg>1-866-555-0148</li>
      <li><svg viewBox="0 0 24 24"><path d="M2 5h20v14H2zm2 2v.5l8 5 8-5V7l-8 5z"/></svg>sales@qelmotorgear.com</li>
      <li><svg viewBox="0 0 24 24"><path d="M12 2a10 10 0 1 0 0 20 10 10 0 0 0 0-20zm0 2c.9 0 2.2 2 2.7 5H9.3C9.8 6 11.1 4 12 4zm-7.7 7h3c0 .7.1 1.4.2 2H4.3a8 8 0 0 1 0-2zm5 0h5.4a12 12 0 0 1 0 2H9.3a12 12 0 0 1 0-2zm7.4 0h3a8 8 0 0 1 0 2h-3c.1-.6.1-1.3 0-2zM9.3 15h5.4c-.5 3-1.8 5-2.7 5s-2.2-2-2.7-5z"/></svg>www.qelmotorgear.com</li>
    </ul>
  </div>
  <address class="address" style="font-style:normal">
    240 W. Harbor Ave.<br>Unit B<br>Fenwick, CA 92800
  </address>
</section>

<section class="card card--back">
  <div class="backdrop-name" aria-hidden="true">QEL</div>
  <div class="back-brand"><span class="back-brand__mark"></span>QEL MOTOR GEAR INC</div>
</section>

</body>
</html>
```